Post it Note design

POST-IT NOTE DESIGN (CONTENT)
Size recommended: 4x6 for handwriting space.
Header (Bold):
Lighting Issue Detected on Your Property
Sub-header:
During our routine night inspection, we noted the following item(s):
Checkbox List:
⬜ Building Lights Out
⬜ Pole Lights Out
⬜ Sign Not Illuminated
⬜ Other ________________________
Action Line:
We can provide a quote or dispatch service right away.
Area for notes
Contact Block (Bold & Centered):
Halverlite Fixture Inc.
Service@HalverliteFixture.com
www.HalverliteFixture.com
877-514-6028
Industry/Entity Type
Electrical lighting
Colors
Designer to choose colors to be used in the design.
Look and feel
Each slider illustrates characteristics of the customer's brand and the style your logo design should communicate.

```html
<!DOCTYPE html>
<html lang="en">
<head>
<meta charset="utf-8">
<title>Halverlite Fixture Inc. – Lighting Issue Notice</title>
<link rel="stylesheet" href="https://fonts.googleapis.com/css2?family=Archivo+Black&family=Arimo:wght@400;500&family=Oswald:wght@300;500&family=Roboto+Condensed:wght@700&display=swap">
<style>
  :root {
    --stage: #3f4f66;
    --paper: #ffffff;
    --brand-blue: #08148a;
    --brand-red: #d0112b;
    --ink: #1c1c1c;
    --silver-light: #eef0f2;
    --silver-dark: #9aa1a8;
  }
  * { margin: 0; padding: 0; box-sizing: border-box; }
  html, body { width: 1097px; height: 1200px; overflow: hidden; background: var(--stage); }
  .note {
    position: absolute; left: 230px; top: 105px; width: 636px; height: 954px;
    background: var(--brand-blue); overflow: hidden;
  }
  .note-header {
    position: absolute; left: 0; top: 0; width: 100%; height: 238px;
    background: var(--paper); border-radius: 0 0 18px 18px;
    display: flex; flex-direction: column; align-items: center; justify-content: center;
  }
  .brand-name {
    font-family: "Archivo Black", sans-serif; color: var(--brand-red);
    font-size: 52px; line-height: 1.04; text-align: center; text-transform: uppercase;
    letter-spacing: -0.5px;
  }
  .headline {
    position: absolute; left: 0; top: 262px; width: 100%; text-align: center;
    font-family: "Archivo Black", sans-serif; color: var(--paper);
    font-size: 34px; line-height: 42px; letter-spacing: 0.6px; text-transform: uppercase;
  }
  .subheader {
    position: absolute; left: 41px; top: 361px; width: 554px; height: 37px;
    background: var(--brand-red); border-radius: 19px; color: var(--paper);
    font-family: "Roboto Condensed", sans-serif; font-weight: 700; font-size: 17.5px;
    display: flex; align-items: center; justify-content: center;
  }
  .note-body {
    position: absolute; left: 0; top: 421px; width: 100%; height: 533px;
    background: var(--paper); border-radius: 18px 18px 0 0; overflow: hidden;
    font-family: Arimo, sans-serif; color: var(--ink);
  }
  .fill-line {
    position: absolute; top: 28px; left: 44px; width: 548px;
    display: flex; align-items: baseline; font-size: 17px; font-weight: 500;
  }
  .fill-line .leader { flex: 1; border-bottom: 2.5px dotted var(--ink); margin: 0 6px 0 10px; }
  .section-title {
    position: absolute; left: 44px; font-family: "Archivo Black", sans-serif;
    color: var(--brand-red); font-size: 23px; letter-spacing: 0.4px; text-transform: uppercase;
  }
  .checklist { position: absolute; left: 44px; top: 126px; width: 560px; list-style: none; }
  .check-item {
    position: absolute; display: flex; align-items: center; font-size: 23px; white-space: nowrap;
  }
  .check-item::before {
    content: ""; width: 16px; height: 16px; border: 1.5px solid var(--brand-blue);
    margin-right: 14px; flex: none;
  }
  .check-item .leader { width: 158px; border-bottom: 3px dotted var(--ink); margin-left: 6px; align-self: flex-end; margin-bottom: 6px; }
  .action-copy { position: absolute; left: 44px; top: 262px; font-size: 22px; line-height: 27px; }
  .burst {
    position: absolute; left: 400px; top: 300px; width: 260px; height: 260px;
    background: radial-gradient(circle, #f4f5f6 0%, #f7f7f8 45%, rgba(255,255,255,0) 70%);
  }
  .contact-band { position: absolute; left: 0; top: 0; width: 636px; height: 954px; pointer-events: none; }
  .contact-name {
    position: absolute; left: 0; top: 792px; width: 249px; height: 29px;
    background: var(--brand-blue); border-radius: 0 15px 15px 0;
    font-family: Oswald, sans-serif; font-weight: 300; font-size: 19px; color: var(--paper);
    padding-left: 44px; line-height: 29px;
  }
  .contact-list { position: absolute; left: 44px; top: 822px; width: 200px; list-style: none; }
  .contact-item {
    display: flex; align-items: center; height: 38.5px; white-space: nowrap;
    font-family: Oswald, sans-serif; font-weight: 500; font-size: 18px; color: var(--paper);
  }
  .contact-item + .contact-item { border-top: 1px dashed rgba(255,255,255,0.7); }
  .contact-item svg { width: 13px; height: 13px; margin-right: 9px; flex: none; }
  .photo {
    position: absolute; left: 336px; top: 710px; width: 300px; height: 244px;
    background: radial-gradient(ellipse at 65% 30%, var(--silver-light) 0%, #c9ced3 40%, var(--silver-dark) 75%, #7e858c 100%);
    border-radius: 110px 0 0 0;
  }
</style>
</head>
<body>
  <article class="note">
    <header class="note-header">
      <div class="brand-name">Halverlite<br>Fixture Inc.</div>
    </header>

    <h1 class="headline">Lighting Issue Detected<br>On Your Property</h1>
    <p class="subheader">During our routine night inspection, we noted the following item(s):</p>

    <section class="note-body">
      <div class="burst"></div>
      <div class="fill-line">
        <span>Date:</span><span class="leader"></span>
        <span>Time:</span><span class="leader"></span>
      </div>

      <h2 class="section-title" style="top:96px">Checkbox List</h2>
      <ul class="checklist">
        <li class="check-item" style="left:0;top:0">Building Lights Out</li>
        <li class="check-item" style="left:266px;top:2px">Sign Not Illuminated</li>
        <li class="check-item" style="left:0;top:42px">Pole Lights Out</li>
        <li class="check-item" style="left:266px;top:44px">Other<span class="leader"></span></li>
      </ul>

      <h2 class="section-title" style="top:229px">Action Line</h2>
      <p class="action-copy">We can provide a quote or dispatch<br>service right away.</p>
    </section>

    <svg class="contact-band" viewBox="0 0 636 954" aria-hidden="true">
      <path d="M0 762 C200 748 400 756 520 790 L580 860 L636 954 L0 954 Z" fill="#ececee"/>
      <path d="M0 770 C180 756 380 764 520 800 C580 845 615 900 636 935 L636 954 L0 954 Z" fill="#d0112b"/>
    </svg>

    <div class="photo" role="img" aria-label="Photo of a technician in a bucket lift servicing a cluster of pole-mounted floodlights"></div>

    <p class="contact-name">Halverlite Fixture Inc.</p>
    <ul class="contact-list">
      <li class="contact-item">
        <svg viewBox="0 0 14 14"><rect x="1" y="3" width="12" height="8" fill="none" stroke="#fff" stroke-width="1.2"/><path d="M1 3 L7 8 L13 3" fill="none" stroke="#fff" stroke-width="1.2"/></svg>
        Service@HalverliteFixture.com
      </li>
      <li class="contact-item">
        <svg viewBox="0 0 14 14"><circle cx="7" cy="7" r="5.8" fill="none" stroke="#fff" stroke-width="1.1"/><ellipse cx="7" cy="7" rx="2.6" ry="5.8" fill="none" stroke="#fff" stroke-width="1"/><path d="M1.2 7 H12.8 M2 4.2 H12 M2 9.8 H12" stroke="#fff" stroke-width="0.9"/></svg>
        www.HalverliteFixture.com
      </li>
      <li class="contact-item">
        <svg viewBox="0 0 14 14"><path d="M4 1.5 L6 1.5 L6.5 4.5 L5 5.3 C5.5 7.5 6.5 9 8.5 10 L9.5 8.7 L12 9.5 L12 12 C7 12.5 2.5 8 3 2.5 Z" fill="none" stroke="#fff" stroke-width="1.1"/></svg>
        877-514-6028
      </li>
    </ul>
  </article>
</body>
</html>
```